Home page design for Drone video business (the Business focusses on home videos for realtors)

Dear reader,

*I NEED DESIGNS OF ALL THE PAGES*
We need a first design of a homepage and of 4 other pages of the website of a business that sells drone video services. All the pages will need to be in the similar design style.
The video's are targeted at consumers that want to sell there home and would like to have a cool drone video of photos of their home.

How does the website look:
- has a navbar on top
- A cool looking banner of an areal drone.
- A Big header: with company name: SkyLoftReels
- A smaller subheader: We film your home to increase your chances of sale
- Then a section with a Big header: How does it work
- In this section a place for a vimeo explainitory video
- Then a similar navbar styled bar with a phone number and a email address
- Then a section where the videos porfolio is displayed in a cool way
- Inside this sectiona header: Our work

- A section with header: Why us?
- 4 symbols here with a subheader and some lorum ipsum text underneath (see wireframe images)

- Under that a: Contact us
- where you can put in name, email, phone, message box and a send button

- At the bottom a footer with phone number and a fake address for now.

Be creative. Use creative but serious color.
Use a serious font. Make it a sharp design. Sharp lines. Not to dark design and not to light design.

The wireframes are the same kind of images.
PLEASE PUT IN DESIGNS OF ALL THE PAGES

Good luck

Target Market(s)

People that want to sell home and want to make a cool drone video or photos of their home.

Industry/Entity Type

Business

Contact Information for Business Card

Lucas Wenning
lucas@skyloftreels.example
+31647208351

Logo Text

SkyLoftReels

Number of Pages Required

1 page

Font styles to use
Sans Serif

Requirements
Must have
• All the sections as explained in the instructions.
• The nav bar should have an about us, services, portfolio and a contact us buttons.
• See instruction for details.
• Must include designs of the front page, contact us, our services, portfolio and contact us.
• If you do add some designs for the "about us", "services", "prices", "portfolio" and "contact us" pages, you make a way better chance of winning the competition.
Nice to have
• designs for the other pages as described at the Must haves. You make a better chance of winning if you include them. Look at the wireframes to see the mockups for those pages. think creative about what kind of sections and design should be included in those pages.
Should not have
• bad designs.

```html
<!DOCTYPE html>
<html lang="en">
<head>
<meta charset="utf-8">
<title>SkyLoftReels — Home</title>
<link href="https://fonts.googleapis.com/css2?family=Lato:wght@400;700;900&display=swap" rel="stylesheet">
<style>
:root{
  --navy:#0d3d6e;
  --blue:#1a5c96;
  --ink:#1e2a36;
  --text:#333;
  --grey-bg:#e6e6e6;
  --bar:#4a4a4a;
  --topbar:#2a2a2a;
  --white:#fff;
  --field:#d9d9d9;
  --footer-base:#1b1b1b;
}
*{margin:0;padding:0;box-sizing:border-box}
html,body{width:1200px;height:2679px;overflow:hidden;background:#fff}
body{font-family:'Lato',sans-serif;color:var(--text);position:relative}
section,header,footer,div,nav,svg.abs{position:absolute}
.topbar{left:0;top:0;width:1200px;height:43px;background:var(--topbar);color:#fff;font-size:14px;font-weight:700}
.topbar .item{top:13px;display:flex;align-items:center;gap:8px}
.site-header{left:0;top:43px;width:1200px;height:87px;background:#fff}
.brand{left:98px;top:26px;font-size:30px;font-weight:700;color:var(--ink);display:flex;align-items:center;gap:10px}
.brand .mark{width:14px;height:14px;background:var(--blue);position:static}
.nav{left:495px;top:36px;display:flex;font-size:14px;font-weight:700;color:var(--ink);white-space:nowrap}
.nav span{margin-right:46px}
.nav .active{color:var(--blue)}
.hero{left:0;top:130px;width:1200px;height:527px;background:linear-gradient(160deg,#6d8a5a 0%,#8a7d70 30%,#7b8590 55%,#4f7a3e 100%)}
.hero-band{left:0;top:388px;width:1200px;height:84px;background:rgba(20,20,20,.72);text-align:center;color:#fff}
.hero-band h1{font-size:40px;font-weight:400;margin-top:6px;letter-spacing:.5px}
.hero-band p{font-size:23px;margin-top:2px}
.how{left:0;top:657px;width:1200px;height:463px;background:var(--grey-bg)}
.how h2{position:absolute;left:104px;top:92px;font-size:30px;font-weight:900;color:var(--ink)}
.how h2 em{font-style:normal;color:var(--blue)}
.how p{position:absolute;left:100px;top:148px;width:445px;font-size:13.5px;line-height:21px;text-align:justify}
.btn{background:var(--navy);color:#fff;font-size:15px;display:flex;align-items:center;justify-content:center}
.how .btn{left:99px;top:343px;width:102px;height:30px}
.laptop{left:509px;top:72px;width:593px;height:340px}
.laptop .screen{left:57px;top:0;width:479px;height:320px;background:#1c1c1c;border-radius:12px}
.laptop .video{left:14px;top:16px;width:451px;height:290px;background:linear-gradient(180deg,#3f6fb4 0%,#7aa0d0 50%,#7d8a5e 100%)}
.laptop .base{left:0;top:320px;width:593px;height:14px;background:linear-gradient(#dcdcdc,#9a9a9a);border-radius:0 0 40px 40px}
.play{width:52px;height:34px;background:var(--blue);border-radius:5px;display:flex;align-items:center;justify-content:center}
.help{left:0;top:1120px;width:1200px;height:82px;background:var(--bar);color:#fff}
.help .divider{top:0;width:1px;height:82px;background:#6a6a6a}
.help .cell{top:27px;display:flex;align-items:center;gap:12px;font-size:22px;white-space:nowrap}
.help .title{left:258px;top:25px;font-size:28px;font-weight:700;text-decoration:underline;text-underline-offset:4px}
.work{left:0;top:1202px;width:1200px;height:420px;background:linear-gradient(180deg,#1c4a78,#25598d 50%,#183f68)}
.section-title{left:0;width:100%;text-align:center;font-size:30px;font-weight:900}
.work .section-title{top:95px;color:#fff}
.thumb{top:155px;width:320px;height:211px;border:3px solid #fff}
.thumb .play{left:131px;top:86px}
.arrow{top:228px}
.why{left:0;top:1622px;width:1200px;height:500px;background:linear-gradient(180deg,#c9d0d6,#d9dde0 40%,#bcc5c9)}
.why .section-title{top:90px;color:var(--ink)}
.feature{width:345px;font-size:12.5px;line-height:20px;color:#222}
.feature h3{font-size:19px;font-weight:700;color:#111;margin-bottom:6px}
.feature.left{text-align:right;left:98px}
.feature.right{left:757px}
.feature b{color:var(--blue)}
.contact{left:0;top:2122px;width:1200px;height:298px;background:linear-gradient(180deg,#2b2e33,#3b3f44 60%,#2d3136)}
.contact h2{position:absolute;left:98px;top:93px;font-size:30px;font-weight:700;color:#fff}
.contact p{position:absolute;left:98px;top:143px;width:392px;font-size:13px;line-height:21px;color:#fff}
.field{background:var(--field);font-size:11px;color:#333;padding:9px 10px}
.contact .btn{left:502px;top:219px;width:120px;height:31px;font-size:20px}
.footer{left:0;top:2420px;width:1200px;height:229px;background:var(--navy);color:#fff}
.footer h4{position:absolute;top:32px;font-size:17px;font-weight:700}
.links{left:98px;top:66px;font-size:13.5px;line-height:27.5px}
.footer .vline{top:50px;width:1px;height:170px;background:#2d5a89}
.detail{left:273px;top:62px;font-size:13.5px;line-height:20px;width:240px}
.detail .row{position:relative;display:flex;gap:10px;align-items:flex-start;margin-bottom:21px}
.map{left:559px;top:59px;width:270px;height:150px;background:linear-gradient(135deg,#e3e3e3,#cfcfcf)}
.foot-brand{left:888px;top:135px;font-size:24px;font-weight:700;color:#fff}
.basebar{left:0;top:2649px;width:1200px;height:30px;background:var(--footer-base);color:#fff;font-size:11px}
.basebar .copy{left:98px;top:9px}
.social{top:5px;width:20px;height:20px;border:1.5px solid #fff;border-radius:50%}
</style>
</head>
<body>

<div class="topbar">
  <div class="item" style="left:787px">
    <svg width="14" height="14" viewBox="0 0 24 24"><path fill="#fff" d="M6.6 10.8a15 15 0 0 0 6.6 6.6l2.2-2.2a1 1 0 0 1 1-.25 11.4 11.4 0 0 0 3.6.57 1 1 0 0 1 1 1V20a1 1 0 0 1-1 1A17 17 0 0 1 3 4a1 1 0 0 1 1-1h3.5a1 1 0 0 1 1 1c0 1.25.2 2.45.57 3.6a1 1 0 0 1-.25 1z"/></svg>
    +31 612 409 375
  </div>
  <div class="item" style="left:937px">
    <svg width="16" height="12" viewBox="0 0 16 12"><rect width="16" height="12" fill="#fff"/><path d="M0 0l8 6 8-6" stroke="#2a2a2a" stroke-width="1.4" fill="none"/></svg>
    hi@skyloftreels.example
  </div>
</div>

<header class="site-header">
  <div class="brand"><span class="mark"></span>SkyLoftReels</div>
  <nav class="nav">
    <span class="active">HOME</span><span>ABOUT US</span><span>SERVICES</span><span>PORTFOLIO</span><span>PRICES</span><span style="margin-right:0">CONTACT US</span>
  </nav>
</header>

<section class="hero" role="img" aria-label="Aerial photo of a large brick house with a drone flying in the foreground">
  <div class="hero-band">
    <h1>SKYLOFTREELS</h1>
    <p>We Film Your Home To Increase Your Chances Of Sale</p>
  </div>
</section>

<section class="how">
  <h2>HOW DOES <em>IT WORK?</em></h2>
  <p>Lorem ipsum dolor sit amet, consectetuer adipiscing elit, sed diam nonummy nibh euismod tincidunt ut laoreet dolore magna aliquam erat volutpat. Ut wisi enim ad minim veniam, quis nostrud exerci tation ullamcorper suscipit lobortis nisl ut aliquip ex ea commodo consequat. Duis autem vel eum iriure dolor in hendrerit in vulputate velit esse molestie consequat, vel illum dolore eu feugiat nulla facilisis at vero eros et accumsan et iusto odio dignissim qui blandit praesent luptatum zzril delenit augue duis dolore te feugait nulla facilisi.</p>
  <div class="btn">Read More »</div>
  <div class="laptop">
    <div class="screen">
      <div class="video" role="img" aria-label="Explainer video still: a man flying a drone in front of a house">
        <div class="play" style="left:200px;top:128px"><svg width="14" height="16" viewBox="0 0 14 16"><path d="M0 0l14 8-14 8z" fill="#fff"/></svg></div>
      </div>
    </div>
    <div class="base"></div>
  </div>
</section>

<section class="help">
  <div class="divider" style="left:484px"></div>
  <div class="divider" style="left:777px"></div>
  <div class="divider" style="left:1102px"></div>
  <div class="title">NEED HELP?</div>
  <div class="cell" style="left:528px">
    <svg width="24" height="24" viewBox="0 0 24 24"><path fill="#fff" d="M6.6 10.8a15 15 0 0 0 6.6 6.6l2.2-2.2a1 1 0 0 1 1-.25 11.4 11.4 0 0 0 3.6.57 1 1 0 0 1 1 1V20a1 1 0 0 1-1 1A17 17 0 0 1 3 4a1 1 0 0 1 1-1h3.5a1 1 0 0 1 1 1c0 1.25.2 2.45.57 3.6a1 1 0 0 1-.25 1z"/></svg>
    +31 612 409 375
  </div>
  <div class="cell" style="left:818px;font-size:19px;top:29px">
    <svg width="36" height="22" viewBox="0 0 40 24"><rect x="0" y="1" width="40" height="22" fill="#fff"/><path d="M0 1l20 12L40 1M0 23l15-10M40 23L25 13" stroke="#4a4a4a" stroke-width="2" fill="none"/></svg>
    hi@skyloftreels.example
  </div>
</section>

<section class="work">
  <div class="section-title">OUR WORK</div>
  <svg class="abs arrow" style="left:48px" width="30" height="60" viewBox="0 0 30 60"><path d="M28 2L4 30l24 28" stroke="#fff" stroke-width="2.5" fill="none"/></svg>
  <svg class="abs arrow" style="left:1120px" width="30" height="60" viewBox="0 0 30 60"><path d="M2 2l24 28L2 58" stroke="#fff" stroke-width="2.5" fill="none"/></svg>
  <div class="thumb" style="left:98px;background:linear-gradient(180deg,#a8bcd0,#7b6a58 55%,#5a6b3f)" role="img" aria-label="Portfolio video: backyard patio with a drone overhead">
    <div class="play"><svg width="14" height="16" viewBox="0 0 14 16"><path d="M0 0l14 8-14 8z" fill="#fff"/></svg></div>
  </div>
  <div class="thumb" style="left:439px;background:linear-gradient(180deg,#b6c8dc,#8a8f8a 50%,#5d6a55)" role="img" aria-label="Portfolio video: operator preparing a drone in a driveway">
    <div class="play"><svg width="14" height="16" viewBox="0 0 14 16"><path d="M0 0l14 8-14 8z" fill="#fff"/></svg></div>
  </div>
  <div class="thumb" style="left:780px;background:linear-gradient(180deg,#c5d6ea,#d8e2ec 45%,#8a96a0)" role="img" aria-label="Portfolio video: white drone hovering near houses">
    <div class="play"><svg width="14" height="16" viewBox="0 0 14 16"><path d="M0 0l14 8-14 8z" fill="#fff"/></svg></div>
  </div>
</section>

<section class="why" role="img" aria-label="Blurred background photo of a drone in flight">
  <div class="section-title">WHY US?</div>
  <svg class="abs" style="left:0;top:0" width="1200" height="500" viewBox="0 0 1200 500">
    <g stroke="#1a5c96" stroke-width="2">
      <line x1="520" y1="227" x2="675" y2="375"/>
      <line x1="675" y1="227" x2="520" y2="375"/>
    </g>
    <circle cx="597" cy="301" r="9" fill="#fff" stroke="#1a5c96" stroke-width="2"/>
    <g fill="#f4f4f4" stroke="#8a8a8a" stroke-width="5">
      <circle cx="520" cy="227" r="52"/><circle cx="675" cy="227" r="52"/>
      <circle cx="520" cy="375" r="52"/><circle cx="675" cy="375" r="52"/>
    </g>
    <g transform="translate(520 227) rotate(-40)" fill="#0d3d6e">
      <path d="M-14-26h28v40l-14 14-14-14z"/>
      <circle cx="0" cy="-17" r="4" fill="#f4f4f4"/>
      <text x="0" y="6" fill="#f4f4f4" font-size="16" font-weight="900" text-anchor="middle" font-family="Lato,sans-serif">%</text>
    </g>
    <g transform="translate(675 227)" fill="none" stroke="#0d3d6e" stroke-width="8">
      <path d="M-14 10a18 18 0 0 1 10-28"/><path d="M14-10a18 18 0 0 1-10 28"/>
      <path d="M-10-26l10 8-10 8z" fill="#0d3d6e" stroke-width="2"/>
      <path d="M10 26l-10-8 10-8z" fill="#0d3d6e" stroke-width="2"/>
    </g>
    <g transform="translate(520 375)">
      <rect x="-22" y="-20" width="40" height="40" rx="4" fill="none" stroke="#0d3d6e" stroke-width="5"/>
      <path d="M-12-2l9 10 22-26" fill="none" stroke="#0d3d6e" stroke-width="7"/>
    </g>
    <g transform="translate(675 375)" fill="#0d3d6e">
      <rect x="-24" y="4" width="9" height="20"/><rect x="-12" y="-4" width="9" height="28"/>
      <rect x="0" y="-12" width="9" height="36"/><rect x="12" y="-18" width="9" height="42"/>
      <path d="M-26 0l14-12 10 6 20-18" fill="none" stroke="#0d3d6e" stroke-width="3"/>
      <path d="M16-28l8 0-2 8z"/>
    </g>
  </svg>
  <div class="feature left" style="top:173px"><h3>CHEAP</h3>Lorem ipsum dolor sit amet, consectetuer adipiscing elit, sed diam nonummy nibh euismod tincidunt ut laoreetfgf dolore magna aliquam erat vol...<b>[+]</b></div>
  <div class="feature right" style="top:173px"><h3>FLEXIBLE</h3>Lorem ipsum dolor sit amet, consectetuer adipiscing elit, sed diam nonummy nibh euismod tincidunt ut laoreetfgf dolore magna aliquam erat vol...<b>[+]</b></div>
  <div class="feature left" style="top:321px"><h3>4 K QUALITY</h3>Lorem ipsum dolor sit amet, consectetuer adipiscing elit, sed diam nonummy nibh euismod tincidunt ut laoreetfgf dolore magna aliquam erat vol...<b>[+]</b></div>
  <div class="feature right" style="top:321px"><h3>INCREASE SALE CHANCES</h3>Lorem ipsum dolor sit amet, consectetuer adipiscing elit, sed diam nonummy nibh euismod tincidunt ut laoreetfgf dolore magna aliquam erat vol...<b>[+]</b></div>
</section>

<section class="contact" role="img" aria-label="Darkened background photo of a house street">
  <h2>CONTACT US</h2>
  <p>Lorem ipsum dolor sit amet, consectetuer auyipiscing elit, s diam nonummy nibyh euismod tinciduntj ut laoreet dolo ma te feugait nulla facilisi. nonummy nibh euismod tincidunt ut laoreet dolo ma te feugait nulla facilisi feugait nulla facilisi. nonummy nibh euismod tincidunt.</p>
  <div class="field" style="left:500px;top:50px;width:288px;height:32px">Name</div>
  <div class="field" style="left:800px;top:50px;width:300px;height:32px">Phone</div>
  <div class="field" style="left:500px;top:93px;width:600px;height:32px">Email</div>
  <div class="field" style="left:500px;top:135px;width:600px;height:74px">Message</div>
  <div class="btn">SEND</div>
</section>

<footer class="footer">
  <h4 style="left:98px">Quick Links</h4>
  <h4 style="left:273px">Contact Detail</h4>
  <h4 style="left:559px">Quick Contact</h4>
  <div class="links">› Home<br>› About Us<br>› Services<br>› Portfolio<br>› Prices<br>› Contact Us</div>
  <div class="vline" style="left:225px"></div>
  <div class="vline" style="left:530px"></div>
  <div class="vline" style="left:858px"></div>
  <div class="detail">
    <div class="row"><svg width="14" height="20" viewBox="0 0 14 20"><path d="M7 0a7 7 0 0 1 7 7c0 5-7 13-7 13S0 12 0 7a7 7 0 0 1 7-7z" fill="#fff"/><circle cx="7" cy="7" r="2.5" fill="#0d3d6e"/></svg><span><b>SkyLoftReels.</b> Lorem ipsum dolor sit amet, consectetuer adipiscing elit</span></div>
    <div class="row"><svg width="14" height="14" viewBox="0 0 24 24"><path fill="#fff" d="M6.6 10.8a15 15 0 0 0 6.6 6.6l2.2-2.2a1 1 0 0 1 1-.25 11.4 11.4 0 0 0 3.6.57 1 1 0 0 1 1 1V20a1 1 0 0 1-1 1A17 17 0 0 1 3 4a1 1 0 0 1 1-1h3.5a1 1 0 0 1 1 1c0 1.25.2 2.45.57 3.6a1 1 0 0 1-.25 1z"/></svg><span>+31 612 409 375</span></div>
    <div class="row"><svg width="16" height="14" viewBox="0 0 16 14"><rect x="3" y="0" width="10" height="4" fill="#fff"/><rect x="0" y="4" width="16" height="7" fill="#fff"/><rect x="3" y="9" width="10" height="5" fill="#fff" stroke="#0d3d6e"/></svg><span>+31 612 409 375</span></div>
    <div class="row"><svg width="16" height="12" viewBox="0 0 16 12"><rect width="16" height="12" fill="#fff"/><path d="M0 0l8 6 8-6" stroke="#0d3d6e" stroke-width="1.4" fill="none"/></svg><span>hi@skyloftreels.example</span></div>
  </div>
  <div class="map" role="img" aria-label="Street map showing the office location"></div>
  <div class="foot-brand">SkyLoftReels</div>
</footer>

<div class="basebar">
  <div class="copy">Copyright © 2016 SkyLoftReels. All Rights Reserved</div>
  <div class="social" style="left:999px"></div>
  <div class="social" style="left:1039px"></div>
  <div class="social" style="left:1079px"></div>
</div>

</body>
</html>
```